Offshore Survey Ship Technical Specification Sheet

We are a provider of specialist survey vessels (ships) to the worldwide oil, gas, telecommunications and renewable energy sectors.

We would like to replace our existing specification sheets that briefly outline the Company information and provide a table of the technical specifications of the ships and survey equipment.

The final design should be two stand-alone documents that are obviously from the same source. The design should be an attractive presentation of each of our ships.

The final deliverable should be provided in an editable format because the vessel and equipment specifications change occasionally and the specification sheets will need to be amended to reflect the changes.

The brochure/specification sheet should cover both sides of a single ISO A4 size sheet.

Our company is based in Iceland and the colour scheme of our vessels reflect the Icelandic flag; blue, red and white.

The ships can be seen on our website.... www.haldrun.is

The existing specification sheets are available here.... http://www.haldrun.is/en/equipment/vessels

The technical specifications and details of equipment shall be provided in a spreadsheet but will be similar in content to the existing spec. sheets.

Images of the vessels are available and will be uploaded along with the Company logo.

If you need any other images, drawings or alternaitve formats (e.g. .eps logo) to support your design ideas then please do not hesitate to contact us.
Updates

Hi

The specification tables have been uploaded.

There are two tabs; one for the ship's equipment and another for the survey equipment.

Many thanks in advance...

Reason: We are very busy with our other operations today.

Hello All

I have uploaded some text in the document 'Brochure Text.doc'.

There are three sections to be added to the designs...

1 .  General text and correct address to be included on both specification sheets
2 .  Specific text for the MV Brekkafell only
3.  Specific text for the MV Skarvik only

We were very busy yesterday and will be again today.  I will try and send comments during today.

Thank You.

Target Market(s)

worldwide oil, gas, telecommunications and renewable energy operators.

Industry/Entity Type

Telecommunications

Requirements
Must have
• Two sides of A4 for each specification sheet - a design of 4 x A4 sides in total (2 specification sheets).

Table of equipment specifications.

```html
<!DOCTYPE html>
<html lang="en">
<head>
<meta charset="utf-8">
<title>Skarvik EA 41 – Vessel Specification</title>
<link href="https://fonts.googleapis.com/css2?family=Carlito:wght@400;700&family=Saira+Semi+Condensed:wght@700&display=swap" rel="stylesheet">
<style>
:root{
  --page:#ffffff;
  --frame:#eceef1;
  --row:#c9d8ea;
  --row-line:#ffffff;
  --small-row:#dce6f1;
  --head:#f7cba4;
  --ink:#1d1d1d;
  --navy:#123f73;
  --label:#7f8b98;
  --value:#2e5d93;
}
*{box-sizing:border-box;margin:0;padding:0}
html,body{width:857px;height:1200px;overflow:hidden;background:var(--frame)}
body{font-family:"Carlito",Calibri,Arial,sans-serif;color:var(--ink);position:relative}
.sheet{position:absolute;left:14px;top:14px;width:829px;height:1172px;background:var(--page)}
.abs{position:absolute}

.hero-photo{left:57px;top:42px;width:707px;height:215px;
  background:linear-gradient(180deg,#8da4bc 0%,#c7d4e0 35%,#e9eef3 52%,#2f5f9a 60%,#f3f3f3 66%,#c9343a 80%,#7a2a2e 100%)}
.vessel-title{right:117px;top:198px;font-family:"Saira Semi Condensed","Arial Narrow",sans-serif;font-weight:700;font-size:26px;line-height:30px;color:#fff;letter-spacing:.5px}

.vessel-details{left:80px;top:257px;width:463px;border-collapse:collapse;background:var(--row);table-layout:fixed}
.vessel-details th{font-size:18px;font-weight:700;text-align:left;padding:0 4px;height:23px;line-height:23px}
.vessel-details td{font-size:15.5px;height:22.5px;padding:0 4px;border-top:1px solid var(--row-line);line-height:16px;white-space:nowrap;overflow:hidden}
.vessel-details td:first-child{width:207px}
.vessel-details tr.tall td{height:23px}
.vessel-details sup{font-size:9px;line-height:0}

.spec{border-collapse:collapse;width:100%;font-size:7.4px;line-height:9.4px;table-layout:fixed}
.spec th{background:var(--head);text-align:left;font-weight:700;font-size:8.6px;padding:1px 2px;color:#111}
.spec td{background:var(--small-row);padding:0 2px;border-top:1px solid #fff;vertical-align:top}
.spec td:first-child{width:48%;border-right:1px solid #fff}
.spec + .spec{margin-top:6px}
.spec sup{font-size:5px;line-height:0}

.right-column{left:527px;top:253px;width:213px}
.right-bar{left:527px;top:573px;width:213px;height:22px;background:var(--navy)}
.left-column{left:80px;top:602px;width:212px}
.left-column .spec + .spec{margin-top:7px}

.survey-photo{left:304px;top:602px;width:436px;height:500px;
  background:radial-gradient(ellipse at 35% 10%,#6d7fa4 0%,#34477a 30%,#1b2a55 70%,#142046 100%)}
.survey-title{right:149px;top:632px;font-family:"Saira Semi Condensed","Arial Narrow",sans-serif;font-weight:700;font-size:23px;line-height:24px;color:#fff;text-align:right}
.survey-card{left:330px;top:703px;width:379px;height:397px;border-radius:22px;background:rgba(255,255,255,.88)}
.kit{left:349px;width:350px;font-size:13px;line-height:13px;display:flex}
.kit dt{width:119px;color:var(--label);flex:none}
.kit dd{color:var(--value)}
</style>
</head>
<body>
<div class="sheet"></div>

<div class="abs hero-photo" role="img" aria-label="Photograph of the survey vessel Skarvik at sea with snowy mountains behind"></div>
<div class="abs vessel-title">SKARVIK AE 41</div>

<table class="abs vessel-details">
  <tr><th colspan="2">Vessel Details</th></tr>
  <tr><td>Name</td><td>Skarvik EA 41</td></tr>
  <tr><td>IMO No.</td><td>7519842</td></tr>
  <tr><td>MMSI No.</td><td>251618320</td></tr>
  <tr><td>Call Sign</td><td>TFKR</td></tr>
  <tr><td>Flag</td><td>Icelandic</td></tr>
  <tr><td>Classification (type)</td><td>Multi-Purpose DP 1 Survey Vessel</td></tr>
  <tr><td>Year built</td><td>1976</td></tr>
  <tr><td>Last overhaul/refit</td><td>2008/2013</td></tr>
  <tr><td>Length overall</td><td>49.85m</td></tr>
  <tr><td>Beam</td><td>9.5m</td></tr>
  <tr><td>Draught</td><td>6.2m</td></tr>
  <tr><td>Tonnage</td><td>1078.63 gross tonnes</td></tr>
  <tr><td>Operating Range</td><td>23460 nautical miles</td></tr>
  <tr class="tall"><td>Main/primary Deck Space</td><td>37m<sup>2</sup></td></tr>
  <tr class="tall"><td>Other/secondary Deck Space</td><td>72m<sup>2</sup></td></tr>
</table>

<div class="abs right-column">
  <table class="spec">
    <tr><th colspan="2">Accommodation Details</th></tr>
    <tr><td>Total Berths</td><td>35</td></tr>
    <tr><td>Total Cabins</td><td>22 + Hospital</td></tr>
    <tr><td>No. Rec Rooms</td><td>1</td></tr>
    <tr><td>No. Gyms</td><td>1</td></tr>
    <tr><td>Online Survey Room</td><td>23m<sup>2</sup></td></tr>
    <tr><td>Offline Survey Room</td><td>14m<sup>2</sup></td></tr>
    <tr><td>Conference Room</td><td>23m2</td></tr>
  </table>
  <table class="spec">
    <tr><th colspan="2">Engine and Machinery</th></tr>
    <tr><td>Main Engine Model</td><td>Boreas B6-300</td></tr>
    <tr><td>Main Engine Power</td><td>1800 HP<br>1320 kW</td></tr>
    <tr><td>Bollard Pull</td><td>28 tonnes</td></tr>
    <tr><td>Aux Engine 1 Model</td><td>Rheinmot R8-550</td></tr>
    <tr><td>Aux Engine 1 Power</td><td>550 HP<br>400 kW</td></tr>
    <tr><td>Aux Engine 2 Model</td><td>Kasumi K6-580</td></tr>
    <tr><td>Aux Engine 2 Power</td><td>580 HP<br>438 kW</td></tr>
    <tr><td>Bow Thruster Power</td><td>330 kW</td></tr>
    <tr><td>Stern Thruster Power</td><td>257 kW</td></tr>
    <tr><td>Max Speed</td><td>12 kts</td></tr>
    <tr><td>Cruising Speed</td><td>11.5 kts</td></tr>
  </table>
  <table class="spec">
    <tr><th colspan="2">Electrical Power</th></tr>
    <tr><td>Aux Generators</td><td>2 x 380 Volts<br>2 x 721 Amps</td></tr>
    <tr><td>Emergency Generator</td><td>230 Volts<br>17.5 Amps</td></tr>
    <tr><td>No.s battery packs</td><td>4</td></tr>
  </table>
</div>
<div class="abs right-bar"></div>

<div class="abs left-column">
  <table class="spec">
    <tr><th colspan="2">Control and Navigation</th></tr>
    <tr><td>Autopilot</td><td>Norvik NP12</td></tr>
    <tr><td>DP System</td><td>Fjordmark DynaSet</td></tr>
    <tr><td>Radar</td><td>Kaito KR 41<br>Kaito KR 52</td></tr>
    <tr><td>Electronic Charts</td><td>ChartWave Vector<br>ChartWave Raster</td></tr>
    <tr><td>DGPS</td><td>Fjordmark Positex FX 40</td></tr>
    <tr><td>GYRO</td><td>Stellan Gyrostar G3<br>Kaito Sat Compass</td></tr>
    <tr><td>MRU</td><td>Fjordmark MRX-2</td></tr>
    <tr><td>Speed Log</td><td>Doppler</td></tr>
    <tr><td>Echo Sounder</td><td>Kaito ES-77</td></tr>
    <tr><td>NAVTEX</td><td>NAVS GMDSS</td></tr>
    <tr><td>AIS</td><td>Kaito AX-9</td></tr>
    <tr><td>Doppler</td><td>Kaito DL-14</td></tr>
  </table>
  <table class="spec">
    <tr><th colspan="2">Communications</th></tr>
    <tr><td>Radio</td><td>2 x VHF Seaward Compact V21<br>2 x VHF Kvist K4</td></tr>
    <tr><td>Internal Radio</td><td>VoxLine System</td></tr>
    <tr><td>Internet</td><td>VSAT OceanLink OL-1</td></tr>
    <tr><td>TV</td><td>VSAT OceanLink OL-2</td></tr>
    <tr><td>Telephone</td><td>V-SAT Sat 2 mb, 512 Kbs. phone</td></tr>
    <tr><td>Additional Comments</td><td>Radio: Seaward HF Suite 250W GMDSS Area A3 with temp A4 Orbitel phone, and Oceansat data and IP telephone network</td></tr>
  </table>
  <table class="spec">
    <tr><th colspan="2">Safety</th></tr>
    <tr><td>Rescue / MOB Boat</td><td>Brimvik<br>25 HP<br>6 persons capacity</td></tr>
    <tr><td>Life Rafts</td><td>4 x Total<br>70 persons total capacity<br>2 x 10 persons capacity<br>2 x 25 persons capacity</td></tr>
    <tr><td>Survival Suits</td><td>35</td></tr>
    <tr><td>Life Jackets</td><td>42</td></tr>
    <tr><td>Work Vest</td><td>7</td></tr>
    <tr><td>Emergency radios/Beacons</td><td>3 x Seaward HB-6</td></tr>
    <tr><td>MOB System</td><td>0.75 tonne davit capacity</td></tr>
  </table>
  <table class="spec">
    <tr><th colspan="2">Deck Machinery</th></tr>
    <tr><td>A-Frame</td><td>10 Tonne<br>8m Clearance Height<br>6m Clearance Width</td></tr>
    <tr><td>Deck Crane</td><td>1.960 tonne @ 9.0m<br>6.200 tonne @ 3.0m<br>9m Reach</td></tr>
  </table>
</div>

<div class="abs survey-photo" role="img" aria-label="Photograph of a survey instrument frame lowered through dark water"></div>
<div class="abs survey-title">SURVEY<br>EQUIPMENT</div>
<div class="abs survey-card"></div>

<dl class="abs kit" style="top:718px"><dt>GNSS</dt><dd>2 x GeoNav G9</dd></dl>
<dl class="abs kit" style="top:744px"><dt>USBL</dt><dd>Hydrix APS<br>2 x HT-1, 3 x HT-2 transponder/beacons</dd></dl>
<dl class="abs kit" style="top:784px"><dt>MRU</dt><dd>Orient Mx4</dd></dl>
<dl class="abs kit" style="top:810px"><dt>MBES</dt><dd>Sonaris Deepscan D2 (deep water)<br>Sonaris Deepscan S1 (shallow water)</dd></dl>
<dl class="abs kit" style="top:850px"><dt>SBES</dt><dd>Aldis Echoline E5</dd></dl>
<dl class="abs kit" style="top:876px"><dt>SVP</dt><dd>2 x Sondar Profiler</dd></dl>
<dl class="abs kit" style="top:903px"><dt>ROV</dt><dd>Brimdal Subrunner Heavy<br>Brimdal Subrunner Mid<br>Brimdal Subrunner Light</dd></dl>
<dl class="abs kit" style="top:955px"><dt>SSS</dt><dd>2 x Sidewave SW-2</dd></dl>
<dl class="abs kit" style="top:981px"><dt>SBP</dt><dd>3x3 hull mounted pinger array</dd></dl>
<dl class="abs kit" style="top:1007px"><dt>Sediment<br>Sampling<br>available on<br>request</dt><dd>Grab Sampler<br>Box Corer<br>Gravity Corer<br>Piston corer<br>CPT<br>Drop Camera</dd></dl>
</body>
</html>
```